Copperbend Blazeworks Website Design

I am looking for a website design ( Home page and inner template page ) in a .psd format. The home page needs to have a large hero image what will function as a "slider", and have some highlight graphical areas/links to the following links "Public & Municipal Events", "Corporate Events", "Special Events". The main navigation needs to have the following nav links "gallery", "home", "about", "services" and "contact". Unfortunately the client does not have any nice hi-rez images ( this is a company that specializes is large fireworks displays ) so please use stock photography sample images from snapvaultpics since we have an account there an can purchase the photos if our client wants to use them. Our current full time graphic artist has been with us for a long time so we are looking at artflockhub as a way to add a fresh approach to design and possibly find someone we can work with regularly. Here is a few designs that in the way we display them for our clients for approval. As you can see there are a couple that don't have their own images so they are utilizing the before mentioned snapvaultpics samples. On the plus side we did manage to get their logo in a .ai format. We have our team for handling the conversion from design to html.

http://reedfoxbuildstudio.com/dev/

```html
<!DOCTYPE html>
<html lang="en">
<head>
<meta charset="utf-8">
<title>Copperbend Blazeworks</title>
<link href="https://fonts.googleapis.com/css2?family=IBM+Plex+Sans:wght@400;500;600&family=Poppins:wght@600;700&display=swap" rel="stylesheet">
<style>
:root{
  --night:#141216;
  --night-deep:#0c0b10;
  --blue:#3a89c4;
  --white:#ffffff;
  --ink:#111111;
  --muted:#d6d6d6;
}
*{margin:0;padding:0;box-sizing:border-box}
html,body{width:1200px;height:2166px;overflow:hidden}
body{position:relative;background:var(--white);font-family:"IBM Plex Sans",sans-serif;color:var(--ink)}
a{color:inherit;text-decoration:none}
.abs{position:absolute}
.btn{position:absolute;display:flex;align-items:center;justify-content:center;background:var(--blue);color:var(--white);font-family:"IBM Plex Sans",sans-serif;font-weight:500;font-size:14px;letter-spacing:.3px}

/* hero */
.hero{position:absolute;left:0;top:0;width:1200px;height:670px;background:var(--night-deep);overflow:hidden}
.hero-photo{position:absolute;left:0;top:290px;width:1200px;height:380px;
  background:
   radial-gradient(circle at 18% 25%,rgba(214,150,70,.55),transparent 12%),
   radial-gradient(circle at 30% 20%,rgba(200,70,160,.45),transparent 11%),
   radial-gradient(circle at 72% 28%,rgba(220,120,60,.45),transparent 10%),
   radial-gradient(circle at 92% 22%,rgba(200,90,190,.5),transparent 12%),
   radial-gradient(circle at 97% 28%,rgba(220,200,90,.4),transparent 10%),
   linear-gradient(180deg,var(--night-deep) 0%,#17161c 60%,#4a3a22 88%,#6b5330 100%)}
.brand{position:absolute;left:132px;top:100px;display:flex;align-items:center;gap:10px;color:var(--white);font-size:26px;font-weight:400}
.brand-dot{width:14px;height:14px;border-radius:50%;background:var(--blue)}
.nav{position:absolute;top:33px;right:132px;display:flex;gap:44px;font-size:15px;font-weight:500;color:var(--white)}
.nav .active{color:var(--blue);text-decoration:underline;text-underline-offset:3px}
.hero-kicker{position:absolute;left:0;width:1200px;top:172px;text-align:center;color:var(--white);font-size:18px;font-weight:500}
.hero-title{position:absolute;left:0;width:1200px;top:212px;text-align:center;color:var(--white);font-size:34px;font-weight:600;letter-spacing:.5px}
.dots{position:absolute;left:562px;top:633px;display:flex;gap:10px;align-items:center}
.dots span{width:6px;height:6px;border-radius:50%;background:var(--white)}
.dots .on{width:10px;height:10px;background:var(--blue);border:2px solid var(--white)}

/* categories */
.section-title{position:absolute;left:0;width:1200px;top:706px;text-align:center;font-family:"Poppins",sans-serif;font-weight:700;font-size:25px}
.card-photo{position:absolute;top:765px;width:301px;height:301px}
.card-label{position:absolute;top:1093px;width:301px;text-align:center;font-size:17px;font-weight:600}

/* about */
.about{position:absolute;left:0;top:1219px;width:1200px;height:463px;
  background:
   radial-gradient(circle at 58% 22%,rgba(200,200,150,.35),transparent 12%),
   radial-gradient(circle at 72% 28%,rgba(220,80,130,.35),transparent 13%),
   radial-gradient(circle at 48% 32%,rgba(230,120,150,.3),transparent 10%),
   radial-gradient(circle at 68% 88%,rgba(140,130,200,.25),transparent 18%),
   linear-gradient(180deg,#16141a 0%,#1a171c 80%,#2a2a30 100%)}
.about-kicker{position:absolute;left:133px;top:1270px;color:var(--white);font-family:"Poppins",sans-serif;font-weight:600;font-size:22px}
.about-title{position:absolute;left:133px;top:1303px;color:var(--white);font-family:"Poppins",sans-serif;font-weight:700;font-size:33px;line-height:38px}
.about-text{position:absolute;left:133px;top:1403px;width:350px;color:var(--white);font-size:15.5px;line-height:22.4px}

/* cta */
.cta{position:absolute;left:0;top:1682px;width:1200px;height:141px;background:var(--blue)}
.cta-text{position:absolute;left:132px;top:1722px;color:var(--white);font-size:19px;line-height:27px}
.cta-btn{position:absolute;left:909px;top:1728px;width:157px;height:49px;border:2px solid var(--white);color:var(--white);display:flex;align-items:center;justify-content:center;font-size:17px;font-weight:500}

/* footer */
.footer{position:absolute;left:0;top:1823px;width:1200px;height:343px;background:linear-gradient(180deg,#0f0e12,#151318)}
.footer-brand{position:absolute;left:132px;top:1985px;display:flex;align-items:center;gap:10px;color:var(--white);font-size:26px}
.col-head{position:absolute;top:1872px;color:var(--white);font-size:13px;font-weight:600;letter-spacing:.5px}
.menu{position:absolute;left:455px;top:1909px;list-style:none;color:var(--muted);font-size:12px;line-height:20px}
.info{position:absolute;display:flex;align-items:center;gap:10px;color:var(--muted);font-size:11.5px;line-height:16px}
.icon{width:24px;height:24px;border-radius:50%;background:var(--white);flex:none;display:flex;align-items:center;justify-content:center}
.rule{position:absolute;left:140px;top:2091px;width:932px;height:1px;background:#2d2b32}
.copy{position:absolute;left:0;width:1200px;top:2124px;text-align:center;color:var(--muted);font-size:9.5px}
</style>
</head>
<body>

<header class="hero">
  <div class="hero-photo" role="img" aria-label="Fireworks bursting over a city skyline at night"></div>
  <a class="brand" href="#"><span class="brand-dot"></span>Copperbend Blazeworks</a>
  <nav class="nav">
    <a class="active" href="#">HOME</a><a href="#">ABOUT</a><a href="#">SERVICES</a><a href="#">GALLERY</a><a href="#">CONTACT</a>
  </nav>
  <p class="hero-kicker">WELCOME TO</p>
  <h1 class="hero-title">COPPERBEND BLAZEWORKS</h1>
  <a class="btn" href="#" style="left:539px;top:277px;width:120px;height:36px;font-size:15px">READ MORE</a>
  <div class="dots"><span></span><span></span><span class="on"></span><span></span><span></span></div>
</header>

<h2 class="section-title">CATEGORIES</h2>
<div class="card-photo" style="left:132px;background:radial-gradient(circle at 50% 35%,#8a8a8e,transparent 45%),linear-gradient(180deg,#2b2b30,#3a2a28)" role="img" aria-label="White fireworks above a crowd at a public event"></div>
<div class="card-photo" style="left:449px;background:radial-gradient(circle at 48% 28%,#d8603c,transparent 28%),linear-gradient(180deg,#1a0e0c,#163235)" role="img" aria-label="Red firework above a lit office tower"></div>
<div class="card-photo" style="left:765px;background:radial-gradient(circle at 45% 42%,#b6ab7a,transparent 40%),radial-gradient(circle at 95% 40%,#a0305a,transparent 22%),#0c0b0f" role="img" aria-label="Golden and pink fireworks over city towers"></div>
<p class="card-label" style="left:132px">PUBLIC &amp; MUNICIPAL EVENTS</p>
<p class="card-label" style="left:441px">CORPORATE EVENTS</p>
<p class="card-label" style="left:761px">SPECIAL EVENTS</p>
<a class="btn" href="#" style="left:229px;top:1138px;width:108px;height:30px">READ MORE</a>
<a class="btn" href="#" style="left:538px;top:1138px;width:108px;height:30px">READ MORE</a>
<a class="btn" href="#" style="left:859px;top:1138px;width:108px;height:30px">READ MORE</a>

<section class="about" role="img" aria-label="Pink and white fireworks over a river at night"></section>
<p class="about-kicker">Welcome to</p>
<h2 class="about-title">COPPERBEND<br>BLAZEWORKS</h2>
<p class="about-text">There are many variations of passages of Lorem Ipsum available, but the majority have suffered alteration in some form, by injected humour, or randomised words which don't look even slightly believable. If you are going to use a passage of Lorem Ipsum</p>
<a class="btn" href="#" style="left:133px;top:1568px;width:107px;height:30px">READ MORE</a>

<section class="cta"></section>
<p class="cta-text">Lorem ipsum dolor sit amet consectetur adipiscing elit sed<br>do eiusmod tempor incididunt ut labore et dolore.</p>
<a class="cta-btn" href="#">CONTACT US</a>

<footer class="footer"></footer>
<div class="footer-brand"><span class="brand-dot"></span>Copperbend Blazeworks</div>

<p class="col-head" style="left:455px">MENU</p>
<ul class="menu"><li>HOME</li><li>ABOUT</li><li>SERVICES</li><li>GALLERY</li><li>CONTACT</li></ul>

<p class="col-head" style="left:655px">CONTACT US</p>
<div class="info" style="left:653px;top:1910px">
  <span class="icon"><svg width="10" height="12" viewBox="0 0 10 12"><path d="M5 0a4 4 0 0 0-4 4c0 3 4 8 4 8s4-5 4-8a4 4 0 0 0-4-4zm0 5.5a1.5 1.5 0 1 1 0-3 1.5 1.5 0 0 1 0 3z" fill="#141216"/></svg></span>
  <span>5127 Larkstone Road<br>Ferrisville, CA 90412</span>
</div>
<div class="info" style="left:653px;top:1962px">
  <span class="icon"><svg width="11" height="11" viewBox="0 0 12 12"><path d="M2.5 1l2 2.3-1 1.3a7 7 0 0 0 3.9 3.9l1.3-1 2.3 2-1 1.5C5.5 11 1 6.5 1 2z" fill="#141216"/></svg></span>
  <span>Call Us<br>555.014.2270</span>
</div>
<div class="info" style="left:653px;top:2013px">
  <span class="icon"><svg width="12" height="9" viewBox="0 0 12 9"><rect x="0.5" y="0.5" width="11" height="8" rx="1" fill="#141216"/><path d="M1 1l5 4 5-4" stroke="#fff" fill="none"/></svg></span>
  <span>E mail Us<br>info@CopperbendBlazeworks.com</span>
</div>

<p class="col-head" style="left:968px">FOLLOW US</p>
<div class="info" style="left:967px;top:1910px"><span class="icon"></span><span>Like us on<br>FRIENDSY</span></div>
<div class="info" style="left:967px;top:1962px"><span class="icon"></span><span>Follow us on<br>CHIRPLINE</span></div>
<div class="info" style="left:967px;top:2013px"><span class="icon"></span><span>Follow us on<br>CAREERLINK</span></div>

<div class="rule"></div>
<p class="copy">Copyright © 2021 All Rights Reserved</p>

</body>
</html>
```